Carpet cleaning company focused on high quality needs business cards

We are a growing company that just merged with another company and need to design a new business card. We do both residential as well as commercial cleaning. We do carpet, tile & grout, upholstery, hard floors, and stain & pet odor removal. We treat our customers like family and strive to achieve outstanding results with every job.

```html
<!DOCTYPE html>
<html lang="en">
<head>
<meta charset="utf-8">
<title>Brightway Steam Care – Business Card</title>
<link rel="stylesheet" href="https://fonts.googleapis.com/css2?family=Open+Sans:wght@400;600;800&family=Ubuntu:wght@700&display=swap">
<style>
  :root {
    --canvas: #e6e6e6;
    --card: #ffffff;
    --ink: #1d1d1d;
    --brand-red: #ef4a3e;
    --brand-blue: #0a86c8;
    --figure-blue: #2c7fc2;
  }
  * { box-sizing: border-box; margin: 0; padding: 0; }
  html, body { width: 1200px; height: 900px; overflow: hidden; }
  body {
    background: var(--canvas);
    font-family: "Open Sans", sans-serif;
    color: var(--ink);
    display: flex;
    flex-direction: column;
    align-items: center;
    justify-content: center;
    gap: 24px;
  }
  .card {
    position: relative;
    width: 760px;
    height: 420px;
    background: var(--card);
    border-radius: 26px;
    overflow: hidden;
    box-shadow: 0 6px 18px rgba(0,0,0,.18);
  }
  .logo { position: absolute; display: flex; align-items: center; }
  .logo-art {
    flex: none;
    border-radius: 4px;
    background: linear-gradient(135deg, var(--brand-red) 0%, var(--brand-red) 55%, var(--figure-blue) 100%);
  }
  .logo-name {
    font-family: "Open Sans", sans-serif;
    font-weight: 800;
    color: var(--ink);
    line-height: 1.02;
    text-transform: uppercase;
    white-space: nowrap;
  }
  .card-front .logo { left: 110px; top: 85px; gap: 26px; }
  .card-front .logo-art { width: 250px; height: 250px; }
  .card-front .logo-name { font-size: 44px; }

  .card-back .logo { left: 40px; top: 125px; gap: 14px; }
  .card-back .logo-art { width: 150px; height: 150px; }
  .card-back .logo-name { font-size: 26px; }

  .divider {
    position: absolute;
    left: 405px; top: 60px;
    width: 2px; height: 200px;
    background: var(--brand-blue);
  }
  .contact { position: absolute; left: 430px; top: 62px; }
  .contact-name {
    font-family: "Ubuntu", sans-serif;
    font-weight: 700;
    font-size: 28px;
    line-height: 1.1;
  }
  .contact-name .first { color: var(--brand-blue); }
  .contact-name .last { color: var(--brand-red); }
  .contact-role { font-size: 17px; margin-top: 2px; }
  .contact-list { list-style: none; margin-top: 12px; font-size: 17px; line-height: 1.5; }
  .contact-list li { display: flex; align-items: center; gap: 8px; }
  .contact-list svg { width: 15px; height: 15px; fill: var(--brand-blue); flex: none; }
  .contact-address { margin-top: 14px; font-size: 17px; line-height: 1.35; padding-left: 23px; }
  .card-stripes { position: absolute; inset: 0; }
</style>
</head>
<body>

<section class="card card-front">
  <div class="logo">
    <div class="logo-art" role="img" aria-label="Illustration of a cheerful cleaning technician holding a steam wand in front of a red square"></div>
    <div class="logo-name">Brightway<br>Steam<br>Care</div>
  </div>
</section>

<section class="card card-back">
  <svg class="card-stripes" viewBox="0 0 760 420" aria-hidden="true">
    <path d="M0 396 L548 342 L554 350 L0 404 Z" fill="var(--brand-red)"/>
    <path d="M0 410 L560 356 C600 352 612 300 662 296 L760 290 L760 420 L0 420 Z" fill="var(--brand-blue)"/>
  </svg>

  <div class="logo">
    <div class="logo-art" role="img" aria-label="Illustration of a cheerful cleaning technician holding a steam wand in front of a red square"></div>
    <div class="logo-name">Brightway<br>Steam<br>Care</div>
  </div>

  <div class="divider"></div>

  <div class="contact">
    <p class="contact-name"><span class="first">Lena</span> <span class="last">Morrow</span></p>
    <p class="contact-role">Executive Director</p>
    <ul class="contact-list">
      <li><svg viewBox="0 0 24 24"><path d="M6.6 10.8a15 15 0 0 0 6.6 6.6l2.2-2.2a1 1 0 0 1 1-.25 11.4 11.4 0 0 0 3.6.57 1 1 0 0 1 1 1V20a1 1 0 0 1-1 1A17 17 0 0 1 3 4a1 1 0 0 1 1-1h3.5a1 1 0 0 1 1 1c0 1.25.2 2.46.57 3.6a1 1 0 0 1-.25 1z"/></svg>123 456 789</li>
      <li><svg viewBox="0 0 24 24"><path d="M2 5h20v14H2z"/><path d="M2 5l10 8 10-8" stroke="#fff" stroke-width="1.5" fill="none"/></svg>info@brightwaysteam.com</li>
      <li><svg viewBox="0 0 24 24"><circle cx="12" cy="12" r="10"/><path d="M2 12h20M12 2c3 3 3 17 0 20M12 2c-3 3-3 17 0 20" stroke="#fff" stroke-width="1.5" fill="none"/></svg>www.brightwaysteam.com</li>
    </ul>
    <p class="contact-address">2710 Harbor Lane<br>Lake Verona,</p>
  </div>
</section>

</body>
</html>
```